Social Media Graphics - Oakline Push REVISED

Create 6-7 individual social media graphics (square size) to encourage folks to join our online course called:

The Harvest Ledger Circle
How to Launch a Multi-Million Business From Scratch
Sign Up Today!

IMPORTANT: Make the largest and most prominent text on the graphic be: How to Launch a Multi-Million Business From Scratch

For the color scheme of the graphics, let's try a blue color palette; make sure the graphics appeal to both men and women

Make sure each graphic contains 1 of the 3 pics attached (crop pic as needed); and make sure one of the graphics is all TEXT only.

Target Market(s)

men and women looking to start a business

Industry/Entity Type

Entrepreneurship

Colors
0054AA
0677BA
7BADD7
CADEEF
E8F1F8

Requirements
Must have
• All the text and use the 3 pics provided; one graphic can be all text; Simple, modern design that's easy to read

```html
<!DOCTYPE html>
<html lang="en">
<head>
<meta charset="utf-8">
<title>The Harvest Ledger Circle — Social Graphics</title>
<link href="https://fonts.googleapis.com/css2?family=Bebas+Neue&display=swap" rel="stylesheet">
<style>
  :root {
    --blue: #0054AA;
    --blue-mid: #0677BA;
    --blue-light: #7BADD7;
    --blue-pale: #CADEEF;
    --blue-mist: #E8F1F8;
    --navy: #043a7a;
    --white: #ffffff;
    --photo-dark: #1c2a44;
    --photo-warm: #5a3c34;
  }
  * { box-sizing: border-box; margin: 0; padding: 0; }
  html, body { width: 1200px; height: 902px; overflow: hidden; background: var(--white); }
  body { position: relative; font-family: "Bebas Neue", "Arial Narrow", sans-serif; }

  .tile { position: absolute; width: 310px; height: 310px; overflow: hidden; color: var(--white); }
  .tile--r1 { top: 143px; }
  .tile--r2 { top: 483px; }
  .tile--c1 { left: 118px; }
  .tile--c2 { left: 461px; }
  .tile--c3 { left: 803px; }

  .tile--navy-fade { background: linear-gradient(180deg, var(--navy) 0%, var(--blue) 75%); }
  .tile--sky-fade { background: linear-gradient(180deg, var(--blue-light) 0%, var(--blue-mid) 100%); }
  .tile--brand { background: var(--blue); }
  .tile--ocean { background: var(--blue-mid); }

  .photo { position: absolute; border-radius: 40px 40px 0 0;
    background: linear-gradient(180deg, var(--photo-warm) 0%, var(--photo-dark) 60%); }

  .badge { position: absolute; width: 58px; height: 58px; margin: -29px 0 0 -29px; border-radius: 50%;
    background: var(--blue); border: 3px solid var(--white); box-shadow: 0 0 6px rgba(232,241,248,.8);
    display: flex; flex-direction: column; align-items: center; justify-content: center;
    font-size: 21px; line-height: 17px; text-align: center; letter-spacing: -0.5px; }
  .badge--large { width: 72px; height: 72px; margin: -36px 0 0 -36px; font-size: 27px; line-height: 22px; }

  .label { position: absolute; display: flex; align-items: center; justify-content: center;
    font-size: 19px; color: var(--blue); white-space: nowrap; }
  .label--pill { left: 27px; top: 126px; width: 256px; height: 42px; background: var(--white); border-radius: 21px;
    box-shadow: 0 -4px 0 -1px var(--white), 0 4px 0 -1px var(--white); }
  .label--trapezoid { left: 50px; top: 148px; width: 210px; height: 34px;
    background: var(--white); clip-path: polygon(6% 0, 94% 0, 100% 100%, 0 100%); }
  .label--framed { left: 47px; top: 128px; width: 218px; height: 42px; background: var(--white); }
  .label--framed span { display: flex; align-items: center; justify-content: center;
    width: 200px; height: 30px; border: 1.5px solid var(--blue-mid); }
  .label--slanted { left: 40px; top: 25px; width: 235px; height: 40px; color: var(--white); font-size: 22px; }
  .label--slanted::before { content: ""; position: absolute; inset: 0; border: 3px solid var(--white);
    background: var(--white); transform: skewX(-8deg); }
  .label--slanted::after { content: ""; position: absolute; inset: 4px 8px; background: var(--blue);
    border: 1.5px solid var(--blue); transform: skewX(-8deg); }
  .label--slanted span { position: relative; z-index: 1; }
  .label--outline { left: 32px; top: 128px; width: 251px; height: 36px; color: var(--white);
    background: var(--blue-mid); border: 1.5px solid var(--white); border-radius: 14px;
    box-shadow: 2px 3px 0 var(--white); }
  .label--boxed { left: 51px; top: 131px; width: 209px; height: 32px; color: var(--white);
    background: var(--blue-mid); border: 1.5px solid var(--white); border-radius: 3px;
    box-shadow: 2px 2px 0 var(--white); }

  .headline { position: absolute; left: 0; width: 100%; text-align: center;
    font-size: 34px; line-height: 37px; letter-spacing: -0.3px; }
  .headline--large { font-size: 40px; line-height: 41px; }
</style>
</head>
<body>

  <section class="tile tile--r1 tile--c1 tile--navy-fade">
    <div class="photo" style="left:94px;top:15px;width:122px;height:110px" role="img" aria-label="Photo of the two course hosts standing with arms crossed"></div>
    <div class="badge" style="left:256px;top:61px"><span>Sign Up</span><span>Today!</span></div>
    <div class="label label--pill">The Harvest Ledger Circle</div>
    <h1 class="headline" style="top:177px">How to Launch a<br>Multi-Million Business<br>From Scratch</h1>
  </section>

  <section class="tile tile--r1 tile--c2 tile--sky-fade">
    <div class="badge" style="left:48px;top:58px"><span>Sign Up</span><span>Today!</span></div>
    <div class="photo" style="left:88px;top:13px;width:132px;height:135px" role="img" aria-label="Photo of the two course hosts smiling, one in black, one in a pink dress"></div>
    <div class="label label--trapezoid">The Harvest Ledger Circle</div>
    <h2 class="headline" style="top:190px">How to Launch a<br>Multi-Million Business<br>From Scratch</h2>
  </section>

  <section class="tile tile--r1 tile--c3 tile--brand">
    <div class="badge" style="left:49px;top:57px"><span>Sign Up</span><span>Today!</span></div>
    <div class="photo" style="left:93px;top:15px;width:125px;height:113px" role="img" aria-label="Photo of the two course hosts standing with arms crossed"></div>
    <div class="label label--framed"><span>The Harvest Ledger Circle</span></div>
    <h2 class="headline" style="top:178px">How to Launch a<br>Multi-Million Business<br>From Scratch</h2>
  </section>

  <section class="tile tile--r2 tile--c1 tile--brand">
    <div class="label label--slanted"><span>The Harvest Ledger Circle</span></div>
    <h2 class="headline headline--large" style="top:80px">How to Launch a<br>Multi-Million Business<br>From Scratch</h2>
    <div class="badge badge--large" style="left:153px;top:253px"><span>Sign Up</span><span>Today!</span></div>
  </section>

  <section class="tile tile--r2 tile--c2 tile--ocean">
    <div class="photo" style="left:85px;top:12px;width:140px;height:116px" role="img" aria-label="Photo of the two course hosts smiling with arms crossed"></div>
    <div class="badge" style="left:262px;top:50px"><span>Sign Up</span><span>Today!</span></div>
    <div class="label label--outline">The Harvest Ledger Circle</div>
    <h2 class="headline" style="top:180px">How to Launch a<br>Multi-Million Business<br>From Scratch</h2>
  </section>

  <section class="tile tile--r2 tile--c3 tile--brand">
    <div class="photo" style="left:70px;top:45px;width:188px;height:83px" role="img" aria-label="Photo of the two course hosts speaking on stage with a microphone"></div>
    <div class="badge" style="left:252px;top:47px"><span>Sign Up</span><span>Today!</span></div>
    <div class="label label--boxed">The Harvest Ledger Circle</div>
    <h2 class="headline" style="top:172px">How to Launch a<br>Multi-Million Business<br>From Scratch</h2>
  </section>

</body>
</html>
```